Business Card Design for Marketing Firm

Looking for business card design for higher end marketing firm. Clean but impressionable/trendy. We are a marketing firm that represents manufacturers in the foodservice equipment and supply industry. Our customers are end users such has hotels, restaurants, country clubs, convention centers and casinos as well as distributors of restaurants supplies and equipment, and manufacturers of foodservice equipment and supplies.
Target Market(s)
Hotels, Restaurants, Supply & Equipment Distributors, Foodservice Manufacturers
Industry/Entity Type
Foodservice/Hospitality
Contact Information for Business Card
Name, Title, Contact Number, Email, Website, Social Media, Address
Requirements
Must have
- Clean & Simple but Serious and Impressionable

```html
<!DOCTYPE html>
<html lang="en">
<head>
<meta charset="utf-8">
<title>Harbor Table Reps — Business Card</title>
<link rel="stylesheet" href="https://fonts.googleapis.com/css2?family=Montserrat:wght@500;600;800&display=swap">
<style>
  :root {
    --stage: #1d1d20;
    --navy: #2b2878;
    --ink: #1a1a24;
    --paper: #ffffff;
  }
  * { box-sizing: border-box; margin: 0; padding: 0; }
  html, body { width: 1200px; height: 900px; overflow: hidden; }
  body {
    background: var(--stage);
    font-family: "Montserrat", sans-serif;
    display: flex; flex-direction: column; align-items: center; justify-content: center;
    gap: 40px;
  }
  .card {
    width: 680px; height: 388px; border-radius: 26px; position: relative; overflow: hidden;
  }
  /* Front */
  .card-front { background: var(--paper); color: var(--ink); }
  .brand-block {
    position: absolute; left: 40px; top: 0; width: 330px; height: 300px;
    display: flex; align-items: center; justify-content: center; gap: 12px;
  }
  .brand-dot { width: 18px; height: 18px; border-radius: 50%; background: var(--navy); flex: none; }
  .brand-name {
    font-weight: 600; font-size: 25px; letter-spacing: 1.5px; color: var(--navy);
    text-transform: uppercase; line-height: 1.2;
  }
  .divider {
    position: absolute; left: 388px; top: 70px; width: 2px; height: 200px; background: var(--navy);
  }
  .contact { position: absolute; left: 412px; top: 70px; font-size: 13.5px; font-weight: 500; line-height: 1.5; }
  .contact-name { font-weight: 800; font-size: 19px; color: var(--navy); letter-spacing: .5px; text-transform: uppercase; }
  .contact-title { margin-bottom: 6px; }
  .contact-row { display: flex; align-items: center; gap: 8px; }
  .contact-row svg { width: 14px; height: 14px; flex: none; fill: var(--navy); }
  .contact-address { margin-bottom: 6px; }
  .social-dot { width: 14px; height: 14px; border-radius: 50%; background: var(--navy); flex: none; }
  .tagline {
    position: absolute; left: 0; right: 0; bottom: 40px; text-align: center;
    font-size: 13px; font-weight: 500; letter-spacing: .2px;
  }
  /* Back */
  .card-back { background: var(--navy); display: flex; align-items: center; justify-content: center; gap: 16px; }
  .card-back .brand-dot { background: var(--paper); width: 24px; height: 24px; }
  .card-back .brand-name { color: var(--paper); font-size: 36px; letter-spacing: 3px; }
</style>
</head>
<body>
  <section class="card card-front" aria-label="Business card front">
    <div class="brand-block">
      <span class="brand-dot"></span>
      <span class="brand-name">Harbor Table<br>Reps</span>
    </div>
    <div class="divider"></div>
    <div class="contact">
      <p class="contact-name">Daniel Morrow</p>
      <p class="contact-title">Co-Founder</p>
      <p class="contact-address">P.O. Box 41-06 NRT-12<br>Linden Ave 8, Fairview</p>
      <p class="contact-row">
        <svg viewBox="0 0 24 24" aria-hidden="true"><path d="M6.6 10.8a15 15 0 0 0 6.6 6.6l2.2-2.2a1 1 0 0 1 1-.25 11.4 11.4 0 0 0 3.6.57 1 1 0 0 1 1 1V20a1 1 0 0 1-1 1A17 17 0 0 1 3 4a1 1 0 0 1 1-1h3.5a1 1 0 0 1 1 1c0 1.25.2 2.45.57 3.57a1 1 0 0 1-.25 1z"/></svg>
        555-014-2290</p>
      <p class="contact-row">
        <svg viewBox="0 0 24 24" aria-hidden="true"><path d="M2 5h20v14H2zm2 2v.4l8 5.3 8-5.3V7zm0 2.8V17h16V9.8l-8 5.3z"/></svg>
        info@harbortablereps.com</p>
      <p class="contact-row">
        <svg viewBox="0 0 24 24" aria-hidden="true"><path d="M12 2a10 10 0 1 0 0 20 10 10 0 0 0 0-20zm6.9 6h-3a15 15 0 0 0-1.3-4A8 8 0 0 1 18.9 8zM12 4c.9 1.2 1.6 2.6 2 4h-4c.4-1.4 1.1-2.8 2-4zM4.3 14a8 8 0 0 1 0-4h3.4a16 16 0 0 0 0 4zm.8 2h3a15 15 0 0 0 1.3 4A8 8 0 0 1 5.1 16zm3-8h-3a8 8 0 0 1 4.3-4 15 15 0 0 0-1.3 4zM12 20c-.9-1.2-1.6-2.6-2-4h4c-.4 1.4-1.1 2.8-2 4zm2.3-6H9.7a14 14 0 0 1 0-4h4.6a14 14 0 0 1 0 4zm.3 6a15 15 0 0 0 1.3-4h3a8 8 0 0 1-4.3 4zm1.7-6a16 16 0 0 0 0-4h3.4a8 8 0 0 1 0 4z"/></svg>
        www.harbortablereps.com</p>
      <p class="contact-row"><span class="social-dot"></span>@harbortablereps</p>
    </div>
    <p class="tagline">Hotels, Restaurants, Supply &amp; Equipment Distributors, Foodservice Manufacturers</p>
  </section>

  <section class="card card-back" aria-label="Business card back">
    <span class="brand-dot"></span>
    <span class="brand-name">Harbor Table Reps</span>
  </section>
</body>
</html>
```